Dental office stationary (letterhead, envelopes), business cards, presentation folders

Nothing too dental outside of the logo. I will need all stationary, presentation folders, business cards. Would prefer to stay in the colors of the logo

Gordon Patel, DDS
Bright Haven Dental Implant Center
555-318-2790
info@brighthavendental.example
4817 NW Maple Crest Rd Unit B
Stuart, FL 00000

Also need appointment date and time
And cancellation policy
I want it to say “kindly ask for
A 48hr cancellation policy to avoid incurring a cancellation fee”

Industry/Entity Type

Dental

Colors
0054AA
0677BA
7BADD7
CADEEF
E8F1F8

Requirements
Must have
• Name of your office, name of doctor, address, phone number
Should not have
• Too much tooth/dental. Only the tooth in logo

```html
<!DOCTYPE html>
<html lang="en">
<head>
<meta charset="utf-8">
<title>Bright Haven Dental Implant Center – Business Card</title>
<link rel="stylesheet" href="https://fonts.googleapis.com/css2?family=Roboto:ital,wght@0,400;0,500;0,700;1,400;1,500;1,700&display=swap">
<style>
  :root {
    --backdrop: #232323;
    --card: #ffffff;
    --teal: #17b294;
    --blue: #1590d6;
    --ink: #3a3a3a;
    --mist: #e8f4fa;
  }
  * { box-sizing: border-box; margin: 0; padding: 0; }
  html, body {
    width: 1200px; height: 900px; overflow: hidden;
    background: var(--backdrop);
    font-family: "Roboto", Arial, sans-serif;
  }
  .sheet {
    width: 1200px; height: 900px;
    display: flex; flex-direction: column;
    align-items: center; justify-content: center; gap: 60px;
  }
  .card {
    position: relative; overflow: hidden;
    width: 616px; height: 352px;
    background: var(--card);
    box-shadow: 0 10px 30px rgba(0,0,0,.45);
  }
  .card-front { display: flex; align-items: center; justify-content: center; }
  .wordmark {
    color: var(--teal); font-weight: 500; text-align: center;
    line-height: 1.05; letter-spacing: .02em;
  }
  .card-front .wordmark { font-size: 46px; }
  .wordmark .wordmark-sub { display: block; font-size: .42em; letter-spacing: .28em; text-transform: uppercase; margin-top: 10px; }
  .card-back .wordmark { position: absolute; left: 42px; top: 34px; font-size: 30px; text-align: left; }
  .card-back .wordmark .wordmark-sub { margin-top: 6px; }
  .backdrop-circle { position: absolute; right: 70px; top: 120px; }
  .address {
    position: absolute; left: 42px; top: 128px;
    font-size: 15px; color: var(--ink); line-height: 1.35;
  }
  .contact-list {
    position: absolute; left: 42px; top: 196px;
    list-style: none; font-size: 15px; color: var(--ink); line-height: 1.5;
  }
  .contact-list li { display: flex; align-items: center; gap: 8px; }
  .contact-list svg { width: 13px; height: 13px; flex: none; }
  .contact-list .web-domain { color: var(--teal); }
  .holder {
    position: absolute; right: 56px; bottom: 62px; text-align: right;
  }
  .holder-name { color: var(--blue); font-weight: 700; font-size: 22px; }
  .holder-practice { color: var(--ink); font-size: 15px; margin-top: 4px; }
  .accent-bar {
    position: absolute; right: 0; bottom: 56px;
    width: 30px; height: 44px; background: var(--teal);
  }
</style>
</head>
<body>
<main class="sheet">
  <section class="card card-front" aria-label="Business card front">
    <div class="wordmark">Bright Haven<span class="wordmark-sub">Dental Implant Center</span></div>
  </section>

  <section class="card card-back" aria-label="Business card back">
    <svg class="backdrop-circle" width="230" height="230" viewBox="0 0 230 230" aria-hidden="true">
      <circle cx="115" cy="115" r="112" fill="var(--mist)"/>
    </svg>
    <div class="wordmark">Bright Haven<span class="wordmark-sub">Dental Implant Center</span></div>
    <p class="address">4817 NW Maple Crest Rd Unit B<br>Stuart, FL 00000</p>
    <ul class="contact-list">
      <li>
        <svg viewBox="0 0 16 16" aria-hidden="true"><path fill="var(--teal)" d="M3 1h3l1.5 4-2 1.2a9 9 0 0 0 4.3 4.3L11 8.5l4 1.5v3a2 2 0 0 1-2 2A12 12 0 0 1 1 3a2 2 0 0 1 2-2z"/></svg>
        555-318-2790
      </li>
      <li>
        <svg viewBox="0 0 16 16" aria-hidden="true"><rect x="1" y="3" width="14" height="10" rx="1" fill="var(--teal)"/><path d="M1.5 4 8 9l6.5-5" stroke="#fff" stroke-width="1.4" fill="none"/></svg>
        info@brighthavendental.example
      </li>
      <li>
        <svg viewBox="0 0 16 16" aria-hidden="true"><circle cx="8" cy="8" r="7" fill="var(--teal)"/><path d="M1 8h14M8 1c3 3.5 3 10.5 0 14M8 1c-3 3.5-3 10.5 0 14" stroke="#fff" stroke-width="1" fill="none"/></svg>
        <span>www.<span class="web-domain">brighthavendental</span>.example</span>
      </li>
    </ul>
    <div class="holder">
      <p class="holder-name">Gordon Patel, DDS</p>
      <p class="holder-practice">Bright Haven Dental Implant Center</p>
    </div>
    <div class="accent-bar"></div>
  </section>
</main>
</body>
</html>
```